Harrowmere Freight, Project

Company Profile
Harrowmere Freight Sdn Bhd is a well established and experienced freight forwarder in Kuala Lumpur, Malaysia. We specialize in air and sea forwarding, Custom Brokerage and regulatory compliance services, inland transportation,
overseas freighting and warehousing and distribution management. With our dedicated qualified and experienced professionals, we are fully committed to serving our clients.

Our Mission
Based on the motto “Quick, Reliable and Polite”, Harrowmere Freight is dedicated to upholding the following three points corporate philosophy:
1. Adhering to the principle that “the customer always comes first”.
2. Contributing to the development of the local community.
3. Making it our duty to be responsible and sincere.

Our Edge
• One-Stop Logistics Solutions
• Extensive Network Throughout Malaysia
• Highly Qualified and Experienced Pool of Professionals
• Comprehensive IT Solutions
• Innovative and Customer-focused Solutions
• Flexible and Consistent in Managing Exceptions
• Total Supply Chain Visibility

Target Market(s)

We sell the logistics services to all the industry in Malaysia. (ONE Stop Logistics Solutions)

Industry/Entity Type

Logistic

Contact Information for Business Card

I want the back of the card to be white with the logo and slogan. i would like to see the logo on the front with the general info.

Requirements
Must have
• Name, Title, Office, Cell, Fax, Email, Address, Website
Nice to have
• Modern Design Business Card

```html
<!DOCTYPE html>
<html lang="en">
<head>
<meta charset="UTF-8">
<title>Harrowmere Freight — Business Card</title>
<link rel="stylesheet" href="https://fonts.googleapis.com/css2?family=Didact+Gothic&family=Questrial&display=swap">
<style>
  :root {
    --backdrop: #55595d;
    --paper: #f2f0e7;
    --paper-white: #fbfaf6;
    --ink: #4a4c4f;
    --ink-soft: #6b6d70;
    --brand-blue: #1f6fb0;
    --accent-blue: #2a8fd0;
    --swoosh-grey: #8d8f92;
    --divider: #cfcbbd;
  }
  * { box-sizing: border-box; margin: 0; padding: 0; }
  html, body { width: 1200px; height: 786px; overflow: hidden; }
  body {
    background: var(--backdrop);
    font-family: "Didact Gothic", "Questrial", sans-serif;
    position: relative;
  }
  .card {
    position: absolute;
    top: 243px;
    width: 525px;
    height: 300px;
    border-radius: 18px;
    overflow: hidden;
    box-shadow: 0 10px 24px rgba(0,0,0,0.35);
  }
  .brand-dot {
    width: 12px; height: 12px; border-radius: 50%;
    background: var(--accent-blue);
    flex: none;
  }
  .brand-name { color: var(--ink); line-height: 1.1; }

  /* Front: contact side */
  .card-front { left: 50px; background: var(--paper); }
  .card-front .swoosh { position: absolute; inset: 0; width: 100%; height: 100%; }
  .front-brand {
    position: absolute;
    left: 40px;
    top: 80px;
    width: 190px;
    display: flex;
    align-items: center;
    gap: 10px;
  }
  .front-brand .brand-name { font-size: 24px; }
  .divider {
    position: absolute;
    left: 250px;
    top: 32px;
    width: 1px;
    height: 140px;
    background: var(--divider);
  }
  .contact {
    position: absolute;
    left: 275px;
    top: 30px;
    color: var(--ink);
  }
  .person-name {
    font-family: "Questrial", sans-serif;
    font-size: 17px;
    letter-spacing: 0.5px;
    color: var(--brand-blue);
    text-transform: uppercase;
  }
  .person-title { font-size: 13px; color: var(--ink-soft); margin-top: 2px; }
  .contact-list { list-style: none; margin-top: 10px; }
  .contact-list li {
    display: flex; align-items: center; gap: 8px;
    font-size: 13px; line-height: 19px;
  }
  .contact-list .label { width: 30px; color: var(--ink-soft); }
  .contact-list svg { width: 13px; height: 13px; flex: none; }
  .address { font-size: 13px; line-height: 18px; margin-top: 8px; }

  /* Back: brand side, white with slogan */
  .card-back {
    left: 625px;
    background: var(--paper-white);
    display: flex; flex-direction: column; align-items: center; justify-content: center; gap: 12px;
  }
  .back-brand { display: flex; align-items: center; gap: 14px; }
  .card-back .brand-dot { width: 16px; height: 16px; }
  .card-back .brand-name { font-size: 36px; }
  .slogan { font-size: 15px; letter-spacing: 1px; color: var(--accent-blue); }
</style>
</head>
<body>
  <section class="card card-front" aria-label="Business card front">
    <svg class="swoosh" viewBox="0 0 525 300" preserveAspectRatio="none" aria-hidden="true">
      <path d="M0 185 C 110 205, 220 240, 335 300 L 0 300 Z" fill="var(--swoosh-grey)"/>
      <path d="M0 170 C 115 195, 225 235, 350 300" fill="none" stroke="var(--accent-blue)" stroke-width="5"/>
    </svg>
    <div class="front-brand">
      <span class="brand-dot"></span>
      <span class="brand-name">Harrowmere Freight</span>
    </div>
    <div class="divider"></div>
    <div class="contact">
      <p class="person-name">Nadia Rahman</p>
      <p class="person-title">General Manager</p>
      <ul class="contact-list">
        <li>
          <svg viewBox="0 0 14 14"><rect width="14" height="14" rx="3" fill="var(--brand-blue)"/><path d="M4 3.5l2 0 .8 2-1.2 1a5 5 0 0 0 2 2l1-1.2 2 .8v2a1 1 0 0 1-1 1A7 7 0 0 1 3 4.5a1 1 0 0 1 1-1z" fill="#fff"/></svg>
          <span class="label">Office</span> 03 7781 2046
        </li>
        <li>
          <svg viewBox="0 0 14 14"><rect width="14" height="14" rx="3" fill="var(--brand-blue)"/><rect x="4.5" y="2.5" width="5" height="9" rx="1" fill="none" stroke="#fff"/></svg>
          <span class="label">Cell</span> 012 508 3917
        </li>
        <li>
          <svg viewBox="0 0 14 14"><rect width="14" height="14" rx="3" fill="var(--brand-blue)"/><rect x="3" y="6" width="8" height="5" fill="none" stroke="#fff"/><rect x="4.5" y="3" width="5" height="3" fill="none" stroke="#fff"/></svg>
          <span class="label">Fax</span> 03 7781 2047
        </li>
        <li>
          <svg viewBox="0 0 14 14"><rect width="14" height="14" rx="3" fill="var(--brand-blue)"/><rect x="3" y="4.5" width="8" height="5.5" fill="none" stroke="#fff"/><path d="M3 4.5l4 3 4-3" fill="none" stroke="#fff"/></svg>
          info@harrowmerefreight.com
        </li>
        <li>
          <svg viewBox="0 0 14 14"><rect width="14" height="14" rx="3" fill="var(--brand-blue)"/><circle cx="7" cy="7" r="4" fill="none" stroke="#fff"/><path d="M3 7h8M7 3v8" stroke="#fff"/></svg>
          www.harrowmerefreight.com
        </li>
      </ul>
      <p class="address">12 Jalan Perdana, Taman Seri<br>Kuala Lumpur, 52100</p>
    </div>
  </section>

  <section class="card card-back" aria-label="Business card back">
    <div class="back-brand">
      <span class="brand-dot"></span>
      <span class="brand-name">Harrowmere Freight</span>
    </div>
    <p class="slogan">Quick, Reliable and Polite</p>
  </section>
</body>
</html>
```